TL - business card

Tallow Partners is an insurance brokerage firm, inovative, proactive, vigorous, which aims to become the leader of the insurance brokers in Anfrica. We should like to get some designs which should be avoided also in Gray / Metallic for the Administration and Orange / Blue for the Managers (ike in the picture sent). The Blue / Green logo is not the correct one, but the source of the file. Please adjust the color accordingly for the business cards. 1 / Orange / Blue 2 / Gray / Metallic We want something classic but which is transmitted strenght, inovation, modernity and most of all, rapidity. We want something start-up like, very punchy and catching eye remaining profesional at the same time. Name: Dorian Whitlock Function: Managing Director Address: N ° 17/18 Rua Veloso - R / C 2B Direita - Bairro Mutamba - Luanda Tel: (+244) 947 582 316 Email: dorian.whitlock@tallow-p.example Website: www.tallow-p. example We want classic in the front and creative, colorfull at the back. The cards will be printed in relief, with very high quality of paper.
Insurance Broker
Colors
Designer to choose colors to be used in the design.

```html
<!DOCTYPE html>
<html lang="en">
<head>
<meta charset="utf-8">
<title>TL - business card</title>
<link href="https://fonts.googleapis.com/css2?family=Exo+2:wght@500;600&family=Lato:wght@400;700&display=swap" rel="stylesheet">
<style>
  :root {
    --backdrop: #2a2a2c;
    --card: #1e1f21;
    --card-back: #1b1c1e;
    --pattern: #222325;
    --orange: #f26a21;
    --blue: #29a9e1;
    --text: #cfd0d2;
    --muted: #a4a6a9;
    --rule: #4a4c4f;
  }
  * { margin: 0; padding: 0; box-sizing: border-box; }
  html, body { width: 1200px; height: 1108px; overflow: hidden; }
  body {
    background: var(--backdrop);
    font-family: "Lato", sans-serif;
    position: relative;
  }
  .card {
    position: absolute;
    top: 239px;
    width: 400px;
    height: 630px;
    border-radius: 22px;
    box-shadow: 0 14px 30px rgba(0,0,0,0.45);
  }
  .card-front { left: 160px; background: var(--card); text-align: center; }
  .card-back { left: 640px; background: var(--card-back); overflow: hidden; }

  .brand {
    position: absolute;
    top: 150px;
    left: 0; right: 0;
    display: flex;
    flex-direction: column;
    align-items: center;
    gap: 18px;
  }
  .brand-dot {
    width: 70px; height: 70px;
    border-radius: 50%;
    border: 5px solid var(--orange);
  }
  .brand-name {
    font-family: "Lato", sans-serif;
    font-weight: 700;
    font-size: 34px;
    letter-spacing: 1px;
    text-transform: uppercase;
    color: var(--orange);
  }
  .person {
    position: absolute;
    top: 352px;
    left: 0; right: 0;
  }
  .person-name {
    font-family: "Exo 2", sans-serif;
    font-weight: 500;
    font-size: 25px;
    letter-spacing: 0.5px;
    text-transform: uppercase;
  }
  .person-name .first { color: var(--orange); }
  .person-name .last { color: var(--blue); }
  .person-role { font-size: 18px; color: var(--text); margin-top: 2px; }
  .divider {
    width: 190px;
    height: 1px;
    background: var(--rule);
    margin: 10px auto;
  }
  .contact, .address {
    font-size: 18px;
    line-height: 1.35;
    color: var(--text);
  }
  .address { color: var(--muted); }

  .back-pattern {
    position: absolute;
    inset: 0;
    background: radial-gradient(circle at 50% 40%, var(--pattern), var(--card-back));
  }
  .back-brand {
    position: absolute;
    left: 0; right: 0;
    top: 470px;
    display: flex;
    flex-direction: column;
    align-items: center;
    gap: 8px;
  }
  .back-brand .brand-dot { width: 44px; height: 44px; border-width: 4px; }
  .back-brand .brand-name { font-size: 14px; }
</style>
</head>
<body>
  <section class="card card-front">
    <div class="brand">
      <span class="brand-dot"></span>
      <span class="brand-name">Tallow Partners</span>
    </div>
    <div class="person">
      <p class="person-name"><span class="first">Dorian</span> <span class="last">Whitlock</span></p>
      <p class="person-role">Managing Director</p>
      <div class="divider"></div>
      <p class="contact">(+244) 947 582 316<br>dorian.whitlock@tallow-p.example</p>
      <div class="divider"></div>
      <p class="address">N ° 17/18 Rua Veloso - R / C<br>2B Direita<br>Bairro Mutamba - Luanda</p>
    </div>
  </section>

  <section class="card card-back">
    <div class="back-pattern" role="img" aria-label="Faint repeating brand pattern in relief across the card back"></div>
    <div class="back-brand">
      <span class="brand-dot"></span>
      <span class="brand-name">Tallow Partners</span>
    </div>
  </section>
</body>
</html>
```